Need business card with a logo for a hearing aid sales and audiology business. We have two Hearing Instrument Specialists and one Audiologist on staff. Over 25 years in business. Locally owned and operated. Financing available. Most insurances accepted.

Summit Audio Wellness LLC
48730 W Larchmont, Suite 7
Spokane, WA 99281
509-617-2084
www.summitaudiowell.example

Manager
Tobias Kerrell HIS COHC
License #71829046

Target Market(s)

50yr old + people with a hearing loss.

Industry/Entity Type

Business

Contact Information for Business Card

48730 W Larchmont, Suite 7
Spokane, WA 99281
509-617-2084
www.summitaudiowell.example

Manager
Tobias Kerrell HIS COHC
NLVE #71829046

Font styles to use
Serif
Sans Serif

Requirements
Must have
• Business name, Tobias's name and title(s) and contact information, License #, web address

```html
<!DOCTYPE html>
<html lang="en">
<head>
<meta charset="utf-8">
<title>Summit Audio Wellness – Business Card</title>
<link href="https://fonts.googleapis.com/css2?family=Open+Sans:wght@400;600;700&display=swap" rel="stylesheet">
<style>
  :root {
    --navy: #1f4b8f;
    --blue: #0f6db8;
    --ink: #333333;
    --rule: #b4b4b4;
    --card: #ffffff;
    --backdrop: #e9e7e4;
  }
  * { margin: 0; padding: 0; box-sizing: border-box; }
  html, body {
    width: 1200px; height: 1000px; overflow: hidden;
    background: var(--backdrop);
    font-family: "Open Sans", Arial, sans-serif;
    color: var(--ink);
  }
  .business-card {
    position: absolute; left: 100px; top: 201px;
    width: 1000px; height: 597px;
    background: var(--card);
    box-shadow: 0 6px 18px rgba(0,0,0,0.18);
    overflow: hidden;
  }
  .brand {
    position: absolute; left: 48px; top: 150px;
    display: flex; align-items: center; gap: 20px;
  }
  .brand-dot {
    width: 58px; height: 58px; border-radius: 50%;
    background: var(--navy);
  }
  .brand-name {
    font-size: 42px; font-weight: 600; color: var(--navy);
    letter-spacing: -0.5px;
  }
  .contact {
    position: absolute; left: 50px; top: 345px;
    font-size: 24px; line-height: 34px;
  }
  .contact-row { display: flex; align-items: center; gap: 12px; }
  .contact-row svg { width: 22px; height: 22px; fill: var(--navy); }
  .address { margin-top: 14px; line-height: 31px; }
  .company { font-weight: 700; }
  .company span { font-weight: 400; }
  .divider {
    position: absolute; left: 270px; top: 359px;
    width: 681px; height: 2px; background: var(--rule);
  }
  .person {
    position: absolute; right: 49px; top: 310px;
    text-align: right; font-size: 24px;
  }
  .person-name {
    font-size: 31px; font-weight: 700; color: var(--navy);
    line-height: 40px; letter-spacing: 0.3px;
  }
  .person-name .credentials {
    font-size: 24px; font-weight: 400; color: var(--blue);
  }
  .person-role { margin-top: 17px; line-height: 39px; }
  .footer-band {
    position: absolute; left: 0; bottom: 0;
    width: 1000px; height: 35px; display: block;
  }
</style>
</head>
<body>
  <div class="business-card">
    <div class="brand">
      <div class="brand-dot"></div>
      <div class="brand-name">Summit Audio Wellness</div>
    </div>

    <div class="contact">
      <div class="contact-row">
        <svg viewBox="0 0 24 24" aria-hidden="true"><path d="M2 9c0-3 4-5 10-5s10 2 10 5v2h-5V8.5c-1.5-.6-3-.8-5-.8s-3.5.2-5 .8V11H2zM6 12l2-3h8l2 3v8H6zm6 2.2a2.3 2.3 0 1 0 0 4.6 2.3 2.3 0 0 0 0-4.6z"/></svg>
        <span>509-617-2084</span>
      </div>
      <div class="contact-row">
        <svg viewBox="0 0 24 24" aria-hidden="true"><path d="M12 2a10 10 0 1 0 0 20 10 10 0 0 0 0-20zm-1 17.9A8 8 0 0 1 4.1 11H7l3 3v2l1 1zm6.9-2.9c-.3-.8-1-1.3-1.9-1.3h-1v-3a1 1 0 0 0-1-1H8v-2h2a1 1 0 0 0 1-1V6h2a2 2 0 0 0 2-2v-.4a8 8 0 0 1 2.9 13.4z"/></svg>
        <span>www.summitaudiowell.example</span>
      </div>
      <div class="address">
        <div class="company">Summit Audio Wellness <span>LLC</span></div>
        <div>48730 W Larchmont, Suite 7</div>
        <div>Spokane, WA 99281</div>
      </div>
    </div>

    <div class="divider"></div>

    <div class="person">
      <div class="person-name">TOBIAS KERRELL <span class="credentials">HIS COHC</span></div>
      <div class="person-role">Manager<br>License #71829046</div>
    </div>

    <svg class="footer-band" viewBox="0 0 1000 35" preserveAspectRatio="none" aria-hidden="true">
      <polygon points="0,0 518,0 483,35 0,35" fill="var(--navy)"/>
      <polygon points="527,0 1000,0 1000,35 492,35" fill="var(--blue)"/>
    </svg>
  </div>
</body>
</html>
```